Sponsorship and registration document for Charity Golf Day 2022

The project requires 2 documents to be updated to look more graphically savvy and professionally presentable.
1. Charity golf day sponsorship document
2. One page registration document.
The text has been completed. Text not to be changed - just graphics.
New images would be preferred.
The logos have been provided.

Target Market(s)

Corporate Sponsors and Golf players

Requirements
Must have
• Golf Theme

```html
<!DOCTYPE html>
<html lang="en">
<head>
<meta charset="utf-8">
<title>Charity Golf Day 2022 – Registration</title>
<link href="https://fonts.googleapis.com/css2?family=Roboto:wght@300;400;500;700&family=Roboto+Condensed:wght@700&display=swap" rel="stylesheet">
<style>
:root{
  --navy:#323f5a;
  --navy-text:#2e3a55;
  --orange:#f0a030;
  --orange-text:#ec9a22;
  --paper:#ffffff;
  --form-bg:#f1f1f1;
  --rule:#6b7285;
  --backdrop:#3f3d3c;
  --grass-dark:#2f5a1c;
  --grass-light:#7aa53a;
  --sky:#e9c98a;
}
*{margin:0;padding:0;box-sizing:border-box}
html,body{width:1200px;height:800px;overflow:hidden;background:var(--backdrop);font-family:'Roboto',sans-serif;color:var(--navy-text)}
.flyer{position:absolute;left:317px;top:0;width:566px;height:800px;background:var(--paper);overflow:hidden}
.abs{position:absolute}
h1,h2,h3{font-weight:400}

.top-band{left:0;top:47px;width:275px;height:24px;background:var(--orange);clip-path:polygon(0 0,263px 0,275px 24px,0 24px)}
.club-mark{right:24px;top:20px;display:flex;align-items:center;gap:8px}
.club-name{text-align:right;color:var(--navy-text);font-weight:400;line-height:1.1}
.club-name .line1{font-size:22px}
.club-name .line2{font-size:14px}
.club-dot{width:44px;height:44px;border-radius:50%;background:var(--orange)}

.hero{left:0;top:71px;width:566px;height:196px;background:var(--navy)}
.hero-photo{left:0;top:71px;width:566px;height:196px;
  clip-path:polygon(275px 0,566px 0,566px 196px,376px 196px);
  background:linear-gradient(180deg,var(--sky) 0%,#b9b27a 22%,var(--grass-light) 40%,var(--grass-dark) 100%)}
.hero-bottom-band{left:231px;top:267px;width:335px;height:11px;background:var(--orange);clip-path:polygon(0 0,335px 0,335px 11px,11px 11px)}
.hero-text{left:20px;top:96px;width:262px;text-align:center;color:#fff}
.hero-title{font-family:'Roboto Condensed',sans-serif;font-weight:700;font-size:29px;line-height:34px;color:var(--orange);letter-spacing:.2px;white-space:nowrap}
.hero-date{font-size:19px;font-weight:500;margin-top:2px;line-height:22px}
.hero-venue{font-size:19px;font-weight:500;line-height:22px}
.hero-rule{width:238px;height:1px;background:#aab0c0;margin:8px auto 10px}
.hero-address{font-size:15px;font-weight:300;line-height:20px}
.hero-url{font-size:15px;font-weight:500;line-height:20px;margin-top:3px}

.intro{left:20px;top:292px;width:311px}
.intro-question{color:var(--orange-text);font-size:14px;line-height:17px;font-weight:400;width:265px}
.intro-rule{width:78px;height:2px;background:var(--orange);margin:8px 0 14px}
.intro-lead{font-size:11.6px;line-height:13.5px;text-align:justify}
.intro-body{font-size:8.6px;line-height:13.3px;margin-top:12px;text-align:justify}
.col-divider{left:348px;top:291px;width:2px;height:164px;background:var(--orange)}

.info{left:368px;top:292px;width:180px}
.info h3{font-size:14px;font-weight:400;color:var(--navy-text)}
.cost-price{font-size:8.8px;font-weight:700;margin-top:4px}
.cost-desc{font-size:8.6px;line-height:10.5px;text-align:justify}
.info .event-head{margin-top:8px}
.schedule{font-size:8.6px;line-height:10.5px;margin-top:1px;display:grid;grid-template-columns:47px 1fr}
.schedule dt{font-weight:700}

.form{left:22px;top:483px;width:527px;height:222px;background:var(--form-bg)}
.form-title{left:29px;top:490px;color:var(--orange-text);font-size:14px;font-weight:400}
.form-title-rule{left:29px;top:508px;width:143px;height:1px;background:var(--orange)}
.form-intro{left:29px;top:512px;font-size:7.8px}
.form-intro strong{font-weight:700}
.field{position:absolute;font-size:7.8px;display:flex;align-items:flex-end;gap:2px}
.field .dots{flex:1;border-bottom:1px dotted var(--rule);height:7px}

.players{position:absolute;left:29px;top:580px;width:510px;border-collapse:collapse;font-size:7.2px}
.players th{background:var(--navy);color:#fff;font-weight:700;height:20px;text-align:center;line-height:7px}
.players th:first-child{border-top-left-radius:6px;text-align:left;padding-left:10px}
.players th:last-child{border-top-right-radius:6px}
.players td{height:18px;border:1px solid var(--navy);font-weight:700;padding-left:6px;vertical-align:bottom;padding-bottom:2px}
.players td:first-child{border-left:2px solid var(--navy)}
.players td:last-child{border-right:2px solid var(--navy)}
.players tr:last-child td{border-bottom:2px solid var(--navy)}

.handicap-note{left:31px;top:682px;font-size:4.9px;font-weight:700}
.cost-line{left:31px;top:695px;font-size:8.6px}
.total-line{left:253px;top:695px;font-size:8.6px}

.payment-title{left:28px;top:717px;font-size:8.6px;font-weight:700}
.check{position:absolute;width:9px;height:9px;border:1px solid var(--navy-text);background:#fff}
.pay-text{position:absolute;font-size:6.6px;line-height:8.2px}
.footer-rule{left:22px;top:763px;width:527px;height:1px;background:var(--rule)}
.fine-print{left:22px;top:767px;width:527px;font-size:4.6px;line-height:7.6px;color:#7a7f8c}
</style>
</head>
<body>
<main class="flyer">
  <div class="abs top-band"></div>
  <div class="abs club-mark">
    <div class="club-name"><div class="line1">Civic Club</div><div class="line2">of Riverdale</div></div>
    <div class="club-dot"></div>
  </div>

  <div class="abs hero"></div>
  <div class="abs hero-photo" role="img" aria-label="Golf ball on the lip of the hole on a green at sunset"></div>
  <div class="abs hero-bottom-band"></div>
  <div class="abs hero-text">
    <h1 class="hero-title">CHARITY GOLF DAY</h1>
    <p class="hero-date">FRIDAY 25 MARCH 2022</p>
    <p class="hero-venue">Elmwood Golf Club</p>
    <div class="hero-rule"></div>
    <p class="hero-address">48 Fairway Road, Hillcrest</p>
    <p class="hero-url">www.ccr.org.au/golf-day</p>
  </div>

  <section class="abs intro">
    <h2 class="intro-question">Do you care about prostate cancer and fighting this disease?</h2>
    <div class="intro-rule"></div>
    <p class="intro-lead">Help us hit prostate cancer off the green and beat the most common cancer in Australian men.Enter a team or as an individual in the 2022 Charity Golf Day.</p>
    <p class="intro-body">Proceeds from this event will be donated to Prostate Cancer Research Group at the Medical Discovery Institute, Eastbrook University, to fund world leading, innovative research and to support men and their families affected by prostate cancer.</p>
  </section>
  <div class="abs col-divider"></div>

  <section class="abs info">
    <h3>COST INFORMATION:</h3>
    <p class="cost-price">$ 150 per player</p>
    <p class="cost-desc">Cost includes golf, light breakfast with coffee/tea on arrival and a two – course lunch following the game.</p>
    <h3 class="event-head">EVENT INFORMATION:</h3>
    <dl class="schedule">
      <dt>EVENT:</dt><dd>4 person Ambrose</dd>
      <dt>7:00am:</dt><dd>Registration</dd>
      <dt>7:15am:</dt><dd>Breakfast</dd>
      <dt>7:45am:</dt><dd>Briefing</dd>
      <dt>8:00am:</dt><dd>Shotgun start</dd>
      <dt>12.30pm:</dt><dd>Lunch</dd>
      <dt>2.00pm:</dt><dd>Presentation/Prizes</dd>
      <dt>3.00pm:</dt><dd>Finish</dd>
    </dl>
  </section>

  <div class="abs form"></div>
  <h2 class="abs form-title">REGISTRATION FORM</h2>
  <div class="abs form-title-rule"></div>
  <p class="abs form-intro">Please complete the details below and return via e-mail to <strong>events@ccr-golfday.org</strong></p>
  <div class="field" style="left:29px;top:524px;width:510px">Name: <span class="dots"></span></div>
  <div class="field" style="left:29px;top:538px;width:510px">Organisation: <span class="dots"></span></div>
  <div class="field" style="left:29px;top:551px;width:510px">Address: <span class="dots"></span></div>
  <div class="field" style="left:29px;top:564px;width:232px">Mobile: <span class="dots"></span></div>
  <div class="field" style="left:265px;top:564px;width:274px">Email: <span class="dots"></span></div>

  <table class="players">
    <colgroup><col style="width:115px"><col style="width:115px"><col style="width:115px"><col style="width:50px"><col style="width:115px"></colgroup>
    <thead><tr><th>NAME OF PLAYERS</th><th>EMAIL</th><th>MOBILE</th><th>GOLF<br>H'CAP</th><th>MEMBER NO.</th></tr></thead>
    <tbody>
      <tr><td>1.</td><td></td><td></td><td></td><td></td></tr>
      <tr><td>2.</td><td></td><td></td><td></td><td></td></tr>
      <tr><td>3.</td><td></td><td></td><td></td><td></td></tr>
      <tr><td>4.</td><td></td><td></td><td></td><td></td></tr>
    </tbody>
  </table>
  <p class="abs handicap-note">PLEASE NOTE: Players without an official Golf Handicap will be given a maximum handicap of 27 (Men) and 36 (Ladies)</p>
  <p class="abs cost-line">COST: $150 per player</p>
  <p class="abs total-line">TOTAL: $.......................</p>

  <h3 class="abs payment-title">METHOD OF PAYMENT</h3>
  <span class="check" style="left:30px;top:729px"></span>
  <p class="pay-text" style="left:44px;top:728px;width:200px">Cheque payable to Civic Club of Riverdale Form and cheque can be mailed to Mara Pellegrino, c/- PO Box 42, Hillcrest Vic 3100</p>
  <span class="check" style="left:266px;top:729px"></span>
  <p class="pay-text" style="left:279px;top:728px">EFT<br>BSB: 102 345<br>Comment:</p>
  <p class="pay-text" style="left:348px;top:736px">Account No: 560 218 447<br>CCRGolf and your surname</p>

  <div class="abs footer-rule"></div>
  <p class="abs fine-print">CANCELLATIONS: Fees are non-refundable or transferable. Substitutions can be made in writing addressed to Mara via email to events@ccr-golfday.org. CCR will only reimburse registration fees if the event is cancelled. CCR is not responsible for any costs incurred as a result. Non-Attendance: If a player fails to attend, fees will not be refunded or allocated to another event.</p>
</main>
</body>
</html>
```